Design a cool print brochure for an NGO / Give your work a global impact!!

Hi,
I provide a full design brief (below, please scroll) and a mood board (attached) to help you visualize inside my head.. ;-)
I am also available to help and have worked many years in advertising; we will understand each other.
Objective:
To design an A4 folded in two presentation brochure for a non-profit consulting agency called Verdomo.
Verdomo works in sustainability and international development = working with NGO’s, governments and private sector on global issues such as global warming, education for all etc.
Strategy:
This document is a first step in developing a communication strategy. It will be distributed during a major international event called the Brightwater Aid Forum.
Objective:
The double objective of the brochure is:
a) to inform the recipient of what Verdomo is, in the shortest time possible.
b) to showcase relevant projects to demonstrate Verdomo experience and expertise.
Target:
Main target:
Existing Verdomo contacts, such as members of development organizations, NGOs, private sector foundations (CSR), regional networks and other development actors.
NB: the main target already has a certain awareness of Verdomo: we will try to minimize text to maximize visual impact and readability.
Secondary target:
Verdomo will also distribute the brochure to new prospects of interest during the Brightwater Forum.
Timing:
We will need to finalize the design and have the files by June 1st to allow time for print before the event.
Content:
The document should be concise, highly readable (no clutter) and include:
1. text (that we will provide)
and
2. visual elements such as images, shapes and info-graphics (that is you).
NB: Verdomo does not have its own image bank; photos will be provided by you.
Format:
A4 folded in half - 4pp A5 - PORTRAIT FORMAT) with an impactful visual in the front, logo, title and headline (please see examples in the mood board attached).
Design elements:
Verdomo does not have yet a visual identity (please see: http://verdomo.org) so there is room for creativity and no graphic chart to follow.
The sector of consulting in international development is rather conservative but our intention is to be disruptive and create a “Wow” effect. We count on you for that!
Therefore, the design should be “structured”, “organized”, “uncluttered” but also “modern”, “impactful”, “highly visual” (think infographic or mind map to describe our services and projects).
Please, take the time to see the attached presentation: I give you guidelines and examples of what we want and what we like.
We are looking forward to seeing your work and I am available for comments, questions and support.
Thank you.
RK
Target Market(s)
The full brief is in the project description: please, scroll through it.
The target market is : our existing clients base, working in sustainable development (read: NGO and Allied Assembly people)
Industry/Entity Type
Ngo
Font styles to use
Requirements
Must have
- - Design and color elements: please, no black and white. Our company website is in black and white and without graphics; we want the brochure to break away from that and start creating our brand identity; so please, show us colors and desing elements (shapes, backgrounds, etc).
- You have a chance to showcase your talent in terms of visual identity: what lines, forms, layout and colors can you come up with and apply throughout the brochure and serve as the visual identity of Verdomo?
- The structure of the document should be:
- - Front cover: design elements + impacful photo (see mood board example attached) +our logo + this headline: "Collective action for sustainable development and impact"
- - Inside front: a graphic representation of "Our Services": such as core activity in the center circle and satellite circles for the services we offer.
- - Inside back:
- 1. Icons and text boxes for "Our projects"
- 2. A world map of the countries where we have worked. Full list of countries is here:
- http://verdomo.org/experience-1
- - Back cover: our contact + logos of partners.
- Our partners are listed here:
- Please use their original logos (ie, in color).
- The design we will select will serve as a basis for a graphic chart...so more work to come...word to the wise ;)
- Please check out our website verdomo.org to see what we do etc.
Nice to have
- Icons to reflect our services: what icons can you come up with to describe "training services", "building networks" or "program management"?
- I give examples in the mood board.
Should not have
- We are open to creativity and want to generate a "Wow" effect.
- Just note that the sector is rather conservative so flashy colors and cartoon like characters should be avoided. Think "earth, global change, Allied Assembly, climate" without going too green (it's overdone). ;-)
- Make us stand out in the NGO world
- Now you.

```html
<!DOCTYPE html>
<html lang="en">
<head>
<meta charset="utf-8">
<title>Verdomo – Brochure</title>
<link href="https://fonts.googleapis.com/css2?family=Fira+Sans:wght@300;400;500;600&family=Signika:wght@400;600&display=swap" rel="stylesheet">
<style>
:root{
  --bg:#e6e6e4;
  --paper:#ffffff;
  --paper-soft:#f1f2f4;
  --navy:#3d5273;
  --navy-deep:#2a2f6b;
  --orange:#e8a33a;
  --grey-logo:#6d6e70;
  --ink:#3b3b3b;
  --badge:#d5dae3;
  --yellow:#f2d25c;
  --red:#ef5a2a;
  --green:#8cc63f;
  --teal:#1b9bb5;
  --magenta:#e0157f;
  --rainbow:linear-gradient(90deg,#2b4a8b 0 8%,#4a9fd5 8% 16%,#5fb85c 16% 24%,#f2c230 24% 32%,#e8683a 32% 40%,#d6246e 40% 48%,#3d5273 48% 56%,#1b9bb5 56% 64%,#8cc63f 64% 72%,#f28c28 72% 80%,#c7244a 80% 88%,#7a3d8f 88% 94%,#e53935 94% 100%);
}
*{box-sizing:border-box;margin:0;padding:0}
html,body{width:854px;height:1200px;overflow:hidden;background:var(--bg)}
body{font-family:"Fira Sans",sans-serif;color:var(--ink);position:relative}

.spread{position:absolute;left:78px;width:710px;height:500px;background:var(--paper);box-shadow:0 3px 10px rgba(0,0,0,.15)}
.spread--outer{top:66px}
.spread--inner{top:628px}
.page{position:absolute;top:0;width:355px;height:100%}
.page--left{left:0}
.page--right{left:355px}
.rainbow{position:absolute;left:0;right:0;bottom:0;height:4px;background:var(--rainbow)}
.lower-tint{position:absolute;left:0;right:0;bottom:4px;height:128px;background:linear-gradient(180deg,#fff,var(--paper-soft))}

.brand{position:absolute;top:34px;left:13px;font-weight:400;font-size:34px;color:var(--grey-logo);letter-spacing:-.5px}

/* outer spread */
.navy-band{position:absolute;left:0;right:0;top:73px;height:295px;background:var(--navy)}
.hero-photo{position:absolute;left:345px;top:79px;width:365px;height:283px;
  background:radial-gradient(circle at 58% 48%,#f4f8fb 0 12%,#9ec2dc 30%,#4c7fa8 55%,#2d4f74 80%);
  clip-path:polygon(12% 0,100% 0,100% 100%,0 100%,4% 60%)}
.projects{position:absolute;left:13px;top:115px;width:285px;color:#fff}
.projects h2{font-family:"Signika",sans-serif;font-weight:600;font-size:11px;color:var(--orange);margin-bottom:15px}
.projects ul{list-style:none}
.projects li{position:relative;padding-left:13px;font-size:7.4px;line-height:1.25;margin-bottom:9.5px;font-weight:300}
.projects li::before{content:"";position:absolute;left:0;top:1.5px;width:6px;height:6px;background:var(--orange)}

.contact{position:absolute;left:13px;top:395px}
.contact h3{font-family:"Signika",sans-serif;font-weight:600;font-size:12px;color:var(--navy);margin-bottom:13px}
.contact p{display:flex;align-items:center;gap:9px;font-size:12px;color:var(--ink);margin-bottom:10px}
.contact svg{width:17px;height:17px}
.partners{position:absolute;left:176px;top:380px;width:170px;border-left:1px solid #c9ccd2;padding-left:18px;height:80px}
.partners .lead{font-size:6.5px;margin:8px 0 10px}
.partners .badges{display:flex;flex-wrap:wrap;gap:6px}
.badge{height:14px;background:var(--badge)}
.badge.circle{width:14px;border-radius:50%}
.headline{position:absolute;left:0;right:0;top:427px;text-align:center;font-family:"Signika",sans-serif;font-weight:600;font-size:15.5px;line-height:1.35;color:var(--navy);letter-spacing:.2px}

/* inner spread */
.section-bar{position:absolute;top:14px;height:39px;left:0;right:0;background:var(--navy);color:#fff;font-family:"Signika",sans-serif;font-weight:600;font-size:15px;padding:13px 0 0 14px}
.field-intro{position:absolute;left:13px;top:62px;width:330px;font-size:7.2px;line-height:1.5;text-align:justify}
.field-intro .q{color:var(--navy);font-weight:500;margin-bottom:9px;text-align:left}
.world-map{position:absolute;left:10px;top:194px;width:330px;height:160px;
  background:radial-gradient(ellipse at 30% 45%,#c3cde3 0 22%,transparent 40%),radial-gradient(ellipse at 70% 40%,#c3cde3 0 25%,transparent 45%),radial-gradient(ellipse at 45% 75%,#d4dbea 0 12%,transparent 28%);border-radius:6px}
.lists{position:absolute;top:372px;left:13px;display:flex;gap:44px}
.lists h4{font-weight:400;font-size:9px;color:var(--orange);margin-bottom:6px}
.lists ul{list-style:none}
.lists li{position:relative;padding-left:10px;font-size:7.3px;line-height:1.5}
.lists li::before{content:"";position:absolute;left:0;top:3px;width:5px;height:5px;background:var(--orange)}

.services-intro{position:absolute;left:14px;top:62px;width:330px;font-size:7.2px;line-height:1.5;text-align:justify}
.service-map{position:absolute;left:0;top:0;width:355px;height:500px}
.service{position:absolute;width:80px;height:55px;border-radius:6px;color:#fff;font-size:6px;font-weight:500;text-align:center;text-transform:uppercase;display:flex;flex-direction:column;align-items:center;justify-content:flex-end;padding:0 4px 8px;box-shadow:0 2px 4px rgba(0,0,0,.15);line-height:1.2}
.service svg{width:20px;height:20px;margin-bottom:6px}
.service--research{left:34px;top:137px;background:var(--yellow)}
.service--training{left:137px;top:137px;background:var(--red)}
.service--knowledge{left:221px;top:137px;background:var(--green)}
.service--coalition{left:34px;top:326px;background:var(--teal)}
.service--evaluation{left:137px;top:326px;background:var(--magenta)}
.service--communication{left:221px;top:326px;background:var(--navy-deep)}
.hub-label{position:absolute;left:90px;top:242px;width:175px;text-align:center;font-weight:400;font-size:30px;color:#fff}
.services-foot{position:absolute;left:0;right:0;top:447px;text-align:center;font-size:7.3px;line-height:1.5;color:var(--navy)}
</style>
</head>
<body>

<section class="spread spread--outer">
  <div class="navy-band"></div>
  <div class="hero-photo" role="img" aria-label="Photo looking up into a glass spiral staircase under a blue sky"></div>
  <div class="lower-tint"></div>

  <div class="page page--left">
    <div class="brand">Verdomo</div>
    <div class="projects">
      <h2>PROJECTS:</h2>
      <ul>
        <li>Advising Belvora in the elaboration of their donor diversification strategy</li>
        <li>Assisting Iberon Institute with the review of the intervention guide of Socialink+ and methodological support to conduct policy dialogue at country level (Europe-Latin America)</li>
        <li>Conducting the mid term evaluation of the multi-country programme NORVALA (strengthening democratic governance and rule of law in Southeast and Eastern Europe) for the Lowland Rights Committee</li>
        <li>Conceptualizing and implementing policy dialogues at country level for the multi-donor programme Climavera+</li>
        <li>Contributing with content, analysis and facilitation to the Open Forum on Progress, a donor funded multi-stakeholder platform</li>
        <li>Feeding the public debate with blogs and specialized articles in relevant media outlets and think tanks, like La Gaceta Diaria, Meridia Geo and Instituto Altamar</li>
      </ul>
    </div>
    <div class="contact">
      <h3>CONTACT US</h3>
      <p><svg viewBox="0 0 20 20"><circle cx="10" cy="10" r="9" fill="#f6d9a8"/><circle cx="10" cy="10" r="6.5" fill="var(--orange)"/><path d="M6.5 8h7v5h-7z M6.5 8l3.5 3 3.5-3" fill="none" stroke="#fff" stroke-width="1"/></svg>info@verdomo.org</p>
      <p><svg viewBox="0 0 20 20"><circle cx="10" cy="10" r="9" fill="#f6d9a8"/><circle cx="10" cy="10" r="6.5" fill="var(--orange)"/><circle cx="10" cy="10" r="3.8" fill="none" stroke="#fff" stroke-width=".9"/><path d="M6.2 10h7.6M10 6.2v7.6" stroke="#fff" stroke-width=".9"/></svg>www.verdomo.org</p>
    </div>
    <div class="partners">
      <p class="lead">Verdomo supports the work of:</p>
      <div class="badges">
        <span class="badge" style="width:32px;height:20px"></span>
        <span class="badge" style="width:40px;height:20px"></span>
        <span class="badge" style="width:34px;height:20px"></span>
        <span class="badge circle" style="width:20px;height:20px"></span>
        <span class="badge" style="width:40px"></span>
        <span class="badge" style="width:34px"></span>
        <span class="badge" style="width:36px"></span>
        <span class="badge circle"></span>
      </div>
    </div>
  </div>

  <div class="page page--right">
    <div class="brand">Verdomo</div>
    <p class="headline">PROMOTING COLLECTIVE ACTION<br>FOR SUSTAINABLE DEVELOPMENT</p>
  </div>
  <div class="rainbow"></div>
</section>

<section class="spread spread--inner">
  <div class="page page--left">
    <div class="section-bar">OUR FIELD</div>
    <div class="field-intro">
      <p class="q">Is it possible to deliver effective solutions in the 21st Century without well-managed collaborative action?</p>
      <p>In Verdomo we consider that, both individually and collectively, we are evolving towards more complex and mixed forms of interaction and organization. Our view is that the intellectual effort to understand that evolution needs to be combined with the practical capacity to take advantage of its great potential: the construction of realistic schemes and environments where both citizens and organizations can participate critically and contribute effectively to the public good.</p>
    </div>
    <div class="world-map" role="img" aria-label="Dotted world map with pins marking countries where Verdomo has worked"></div>
    <div class="lists">
      <div>
        <h4>We specialize in:</h4>
        <ul>
          <li>Policy dialogue</li>
          <li>Donor diversification strategies</li>
          <li>Multi-stakeholder partnerships</li>
          <li>Strategic partnerships</li>
          <li>Framework agreements</li>
          <li>Goal-directed networks</li>
        </ul>
      </div>
      <div>
        <h4>We work with:</h4>
        <ul>
          <li>International Organizations</li>
          <li>Private sector companies</li>
          <li>NGOs</li>
          <li>Trade unions</li>
          <li>Universities and Think tanks</li>
          <li>Regional and Local governments</li>
          <li>Development agencies</li>
        </ul>
      </div>
    </div>
  </div>

  <div class="page page--right">
    <div class="section-bar">OUR SERVICES</div>
    <p class="services-intro">Verdomo is a response to the growing need of a wide array of organizations to understand changes in the development landscape, undergo structural changes, improve processes and increase the impact of their participation in collective actions to attain development goals.</p>

    <svg class="service-map" viewBox="0 0 355 500" aria-hidden="true">
      <g fill="none" stroke="#b8bcc4" stroke-width="1">
        <path d="M74 198v8h50v14"/>
        <path d="M177 198v22"/>
        <path d="M261 198v8h-50v14"/>
        <path d="M74 320v-8h50v-14"/>
        <path d="M177 320v-22"/>
        <path d="M261 320v-8h-50v-14"/>
      </g>
      <g>
        <circle cx="74" cy="198" r="2.2" fill="var(--yellow)"/><circle cx="124" cy="220" r="2.2" fill="var(--yellow)"/>
        <circle cx="177" cy="198" r="2.2" fill="var(--red)"/><circle cx="177" cy="220" r="2.2" fill="var(--red)"/>
        <circle cx="261" cy="198" r="2.2" fill="var(--green)"/><circle cx="211" cy="220" r="2.2" fill="var(--green)"/>
        <circle cx="124" cy="298" r="2.2" fill="var(--teal)"/><circle cx="74" cy="320" r="2.2" fill="var(--teal)"/>
        <circle cx="177" cy="298" r="2.2" fill="var(--magenta)"/><circle cx="177" cy="320" r="2.2" fill="var(--magenta)"/>
        <circle cx="211" cy="298" r="2.2" fill="var(--navy-deep)"/><circle cx="261" cy="320" r="2.2" fill="var(--navy-deep)"/>
      </g>
      <rect x="78" y="224" width="186" height="72" rx="36" fill="none" stroke="#a7abb3" stroke-width="2.5"/>
      <rect x="88" y="234" width="166" height="52" rx="26" fill="var(--navy)"/>
    </svg>
    <div class="hub-label">Verdomo</div>

    <div class="service service--research"><svg viewBox="0 0 20 20" fill="none" stroke="#fff" stroke-width="1.4"><circle cx="10" cy="10" r="8"/><circle cx="10" cy="10" r="4.5"/><circle cx="10" cy="10" r="1.3" fill="#fff"/><path d="M10 10l8-8"/></svg>Research and analysis</div>
    <div class="service service--training"><svg viewBox="0 0 20 20" fill="#fff"><circle cx="5" cy="7" r="2.3"/><circle cx="10" cy="5" r="2.5"/><circle cx="15" cy="7" r="2.3"/><path d="M1 15c0-3 2-4.5 4-4.5s4 1.5 4 4.5zM6 13c0-3.5 2-5 4-5s4 1.5 4 5zM11 15c0-3 2-4.5 4-4.5s4 1.5 4 4.5z"/></svg>Facilitation and training</div>
    <div class="service service--knowledge"><svg viewBox="0 0 20 20" fill="none" stroke="#fff" stroke-width="2"><circle cx="7" cy="12" r="3.5" stroke-dasharray="2 1.2"/><circle cx="14" cy="6" r="2.8" stroke-dasharray="1.6 1"/></svg>Knowledge management</div>
    <div class="service service--coalition"><svg viewBox="0 0 20 20"><circle cx="10" cy="10" r="9" fill="#fff"/><path d="M10 4l2.5 6H7.5zM4.5 14l4-3 1 2.5zM15.5 14l-4-3-1 2.5z" fill="var(--teal)"/></svg>Coalition building</div>
    <div class="service service--evaluation"><svg viewBox="0 0 20 20" fill="none" stroke="#fff" stroke-width="1.4"><rect x="2" y="5" width="13" height="9"/><path d="M1 16h15M5 11l3-3 2 2 3-3"/><rect x="14" y="2" width="4" height="4" fill="#fff"/></svg>Evaluation</div>
    <div class="service service--communication"><svg viewBox="0 0 20 20" fill="none" stroke="#fff" stroke-width="1.5"><circle cx="10" cy="10" r="3"/><circle cx="10" cy="10" r="7.5" stroke-dasharray="2.5 1.5"/></svg>Communication</div>

    <p class="services-foot">In Verdomo we believe that theory cannot be separated from practice. The real<br>background of our work is trying to adapt models to a changing reality.</p>
  </div>
  <div class="rainbow"></div>
</section>

</body>
</html>
```